Dynamic Business Card for Sports Supplements Company

Hi! I'm looking for an awesome business card to match my existing sports supplement company. I have uploaded my current company logo and screenshot of the front page of my website.

I would like to have something dynamic and interesting and utilize the colors in the website - the reds and purples

The business card should be double sided and focus on a unique eye-catching design on the back and include all the relevant company info.

Most importantly, it should say somewhere: "Sign up on our website for a coupon code."

Target Market(s)

Mostly for women gym goers but it shouldn't be too feminine. It should be in keeping with the website design. It should flow and clearly be connected to it

Industry/Entity Type

Business

Contact Information for Business Card

Lorraine K. Vestal
CEO
LVestal@Quorvanexco.com
www.quorvanexco.com
555.417.3820
P.O. Box 47315
Alderton, Westmark 00000

Sign up on our website for a coupon code

Font styles to use
Serif
Sans Serif
Other font styles liked:
• Novecento font family and "Quorvanex" is in AR Destine font

Requirements
Must have
• One side should be a bold Quorvanex logo design. Even just the symbol itself may be o.k. (see attached file)

```html
<!DOCTYPE html>
<html lang="en">
<head>
<meta charset="utf-8">
<title>Quorvanex Business Card</title>
<link rel="stylesheet" href="https://fonts.googleapis.com/css2?family=Exo+2:ital,wght@0,400;0,500;0,700;0,800;1,600&display=swap">
<style>
  :root {
    --stage: #2b2b2d;
    --card-dark: #1c1c1e;
    --pattern-tone: #262628;
    --card-light: #ffffff;
    --brand-red: #e3262b;
    --ink: #3a3a3c;
    --white: #ffffff;
  }
  * { box-sizing: border-box; margin: 0; padding: 0; }
  html, body {
    width: 1200px; height: 1000px; overflow: hidden;
    background: var(--stage);
    font-family: "Exo 2", sans-serif;
  }
  .card {
    position: absolute; left: 290px;
    width: 620px; height: 354px;
    overflow: hidden;
    box-shadow: 0 8px 24px rgba(0,0,0,.45);
  }

  /* Back side */
  .card--back { top: 70px; background: var(--card-dark); }
  .back__texture {
    position: absolute; inset: 0;
    background: linear-gradient(135deg, var(--pattern-tone), var(--card-dark) 60%, var(--pattern-tone));
  }
  .back__brand {
    position: absolute; left: 0; right: 0; top: 128px;
    text-align: center; color: var(--white);
  }
  .back__mark {
    display: inline-block; width: 26px; height: 26px;
    background: var(--brand-red); margin-bottom: 14px;
  }
  .back__name {
    font-weight: 800; font-size: 46px; letter-spacing: 2px; line-height: 1;
  }
  .back__tagline {
    font-weight: 500; font-size: 19px; letter-spacing: 1.5px; margin-top: 4px;
  }

  /* Front side */
  .card--front { top: 560px; background: var(--card-light); }
  .front__brand { position: absolute; left: 40px; top: 34px; color: var(--brand-red); }
  .front__name { font-weight: 800; font-size: 44px; letter-spacing: 2px; line-height: 1; }
  .front__tagline { font-weight: 500; font-size: 18px; letter-spacing: 1.8px; margin-top: 2px; }
  .front__divider {
    position: absolute; left: 40px; right: 0; top: 160px;
    height: 2px; background: var(--brand-red);
  }
  .contact-list {
    position: absolute; left: 40px; top: 186px;
    list-style: none; font-size: 15px; color: var(--ink); line-height: 24px;
  }
  .contact-list li { display: flex; align-items: center; gap: 10px; }
  .contact-list svg { width: 14px; height: 14px; fill: var(--brand-red); flex: none; }
  .contact-list .accent { color: var(--brand-red); }
  .person {
    position: absolute; right: 54px; top: 184px; text-align: right;
  }
  .person__name {
    font-weight: 700; font-size: 22px; letter-spacing: 1px; color: var(--brand-red);
    padding-bottom: 4px; border-bottom: 2px solid var(--brand-red);
  }
  .person__role { font-size: 15px; color: var(--ink); margin-top: 2px; }
  .address {
    position: absolute; right: 54px; top: 256px;
    display: flex; gap: 12px; font-size: 15px; line-height: 21px;
    color: var(--ink); text-align: right;
  }
  .address svg { width: 13px; height: 13px; fill: var(--brand-red); margin-top: 3px; }
  .promo-band {
    position: absolute; left: 0; right: 0; bottom: 0; height: 34px;
    background: var(--brand-red);
  }
  .promo-band__text {
    position: absolute; left: 40px; top: 0; line-height: 34px;
    color: var(--white); font-style: italic; font-weight: 600;
    font-size: 13px; letter-spacing: 1px; text-transform: uppercase;
  }
  .promo-band__cut {
    position: absolute; left: 418px; top: -4px; width: 8px; height: 44px;
    background: var(--card-light); transform: skewX(-35deg);
  }
</style>
</head>
<body>

  <section class="card card--back">
    <div class="back__texture" role="img" aria-label="Subtle repeating dark brand pattern across the card background"></div>
    <div class="back__brand">
      <span class="back__mark"></span>
      <div class="back__name">QUORVANEX</div>
      <div class="back__tagline">your strength companion</div>
    </div>
  </section>

  <section class="card card--front">
    <div class="front__brand">
      <div class="front__name">QUORVANEX</div>
      <div class="front__tagline">your strength companion</div>
    </div>
    <div class="front__divider"></div>

    <ul class="contact-list">
      <li>
        <svg viewBox="0 0 16 16"><path d="M3 1l3 3-1.5 2a9 9 0 005.5 5.5L12 10l3 3-2 2C7 15 1 9 1 3z"/></svg>
        555.417.3820
      </li>
      <li>
        <svg viewBox="0 0 16 16"><path d="M1 3h14v10H1zM2 4.5v.3l6 4 6-4v-.3z"/></svg>
        LVestal@Quorvanexco.com
      </li>
      <li>
        <svg viewBox="0 0 16 16"><path d="M10 1a5 5 0 11-3.3 8.8L2.4 14.1 1 12.7l4.3-4.3A5 5 0 0110 1zm0 2a3 3 0 100 6 3 3 0 000-6z"/></svg>
        <span>www.<span class="accent">quorvanexco</span>.com</span>
      </li>
    </ul>

    <div class="person">
      <div class="person__name">LORRAINE K. VESTAL</div>
      <div class="person__role">CEO</div>
    </div>

    <div class="address">
      <svg viewBox="0 0 16 16"><path d="M15 1L1 7l6 2 2 6z"/></svg>
      <div>P.O. Box 47315 Alderton,<br>Westmark 00000</div>
    </div>

    <div class="promo-band">
      <span class="promo-band__text">Sign up on our website for a coupon code</span>
      <span class="promo-band__cut"></span>
    </div>
  </section>

</body>
</html>
```